Redesign This Psychology Website

We would like a slight redesign of this successful psychology (relationship counselling) website:

www.TheKelvaleClinic.com.au

We are updating the website, and we'd like a slight refresh of the design and style.

Please keep to very similar colours, and use the same logo. We're looking for around 10 page templates, however the main one is the home page.

Keep in mind, this website already converts quite well, so we want a new, fresh design in keeping with this one. Please don't bother designing something too extremely different.

thanks :)

Target Market(s)

couples who are looking for relationship counselling. Men and women, 25 - 70, across Australia

Industry/Entity Type

Psychology

Number of Pages Required

5+ page

Font styles to use
Sans Serif

Colors
87cfc6
b7a5cd
ec1f27
ffffff
cee9f5

Requirements
Must have
• a similar look to the current design, just looking for a slight refresh.
• Search bar
• Areas for lots of photos
• same logo
• lots of content areas
Nice to have
• great content areas, where we can display a lot of content and our areas.
Should not have
• no colors like orange, etc.
• should not have a totally different feel.

```html
<!DOCTYPE html>
<html lang="en">
<head>
<meta charset="utf-8">
<title>The Kelvale Clinic – Sex Therapy Sydney</title>
<link href="https://fonts.googleapis.com/css2?family=Montserrat:wght@400;500;600&family=Open+Sans:wght@400;600;700&display=swap" rel="stylesheet">
<style>
:root{
  --teal:#87cfc6;
  --teal-dark:#5dbcb2;
  --teal-text:#2f9c9c;
  --purple:#b7a5cd;
  --red:#ec1f27;
  --sky:#cee9f5;
  --white:#ffffff;
  --ink:#333333;
  --body:#6b6b6b;
  --line:#d9d9d9;
  --grey-bg:#f2f2f2;
}
*{box-sizing:border-box;margin:0;padding:0}
html,body{width:1200px;height:3644px;overflow:hidden}
body{position:relative;background:var(--white);font-family:"Open Sans",Arial,sans-serif;color:var(--body);font-size:12.5px;line-height:1.75}
.abs{position:absolute}
a{color:inherit;text-decoration:none}

/* top bar */
.top-bar{left:0;top:0;width:1200px;height:48px;background:var(--grey-bg);border-bottom:1px solid #e4e4e4}
.top-bar .associate{position:absolute;left:133px;top:13px;font-size:14px;color:#666}
.top-links{position:absolute;right:128px;top:0;display:flex;height:48px;align-items:center}
.top-links a{font-size:13px;color:#777;padding:0 12px;border-left:1px solid #d5d5d5}
.top-links a:first-child{border-left:none}

/* header */
.brand{left:116px;top:64px;display:flex;align-items:center;gap:12px}
.brand .mark{width:54px;height:54px;border-radius:50%;background:var(--teal-dark);flex:none}
.brand .name{font-family:"Montserrat",sans-serif;font-weight:500;font-size:28px;color:var(--teal-text);line-height:1;white-space:nowrap}
.brand .tagline{font-family:"Montserrat",sans-serif;font-weight:500;font-size:12.5px;color:var(--teal-text);margin-top:6px;white-space:nowrap}
.search{left:457px;top:85px;width:357px;height:40px;border:1px solid #d6d6d6;border-radius:3px;display:flex;align-items:center;padding-left:14px;gap:10px;color:#9a9a9a;font-size:13px}
.call{right:128px;top:72px;text-align:right;font-family:"Montserrat",sans-serif}
.call .label{font-size:15px;color:var(--teal)}
.call .num{display:flex;align-items:center;gap:8px;font-size:24px;color:var(--teal-text);line-height:1.1}

/* nav */
.main-nav{left:0;top:163px;width:1200px;height:66px;background:linear-gradient(var(--teal),var(--teal-dark));display:flex;padding-left:120px}
.main-nav a{color:var(--white);font-family:"Montserrat",sans-serif;font-weight:500;font-size:15px;line-height:1.2;padding:12px 16px 0;border-right:1px solid rgba(255,255,255,.45);text-transform:uppercase;height:66px}
.main-nav a:last-child{border-right:none}

/* hero */
.hero{left:0;top:229px;width:1200px;height:326px;background:linear-gradient(100deg,#6f6a64 0%,#b69a86 35%,#d8c3b1 55%,#8fa6b8 80%,#5f7184 100%)}
.hero h1{position:absolute;left:150px;top:170px;font-family:"Montserrat",sans-serif;font-weight:400;font-size:32px;color:rgba(255,255,255,.75);letter-spacing:1px;text-transform:uppercase}

/* main column */
.main{left:126px;width:590px}
.main p{margin-bottom:10px}
h2.page-title{font-family:"Montserrat",sans-serif;font-weight:400;font-size:27px;line-height:1.3;color:var(--ink)}
.portrait{left:457px;top:610px;width:268px;height:268px;border-radius:50%;background:radial-gradient(circle at 45% 40%,#c9a994,#7a5c4c 70%,#4c3c36)}
h3.alert{font-family:"Montserrat",sans-serif;font-weight:400;font-size:22px;line-height:1.5;color:var(--red)}
h3.section{font-family:"Montserrat",sans-serif;font-weight:400;font-size:24px;color:var(--teal-text)}
.lead{color:var(--ink);font-weight:600}

/* office grid */
.offices{left:134px;top:2432px;width:582px;display:grid;grid-template-columns:284px 284px;gap:12px 14px}
.office{height:150px;border:1px solid #cfcfcf;background:linear-gradient(#ffffff,#ececec);padding:22px 0 0 26px;font-size:12.5px;line-height:1.7;color:#777}
.office strong{display:block;color:var(--ink);font-weight:600;text-transform:uppercase}

/* sidebar */
.finder{left:768px;top:600px;width:304px;height:360px;background:var(--purple);padding:20px 28px;color:var(--white)}
.finder h4{font-family:"Montserrat",sans-serif;font-weight:500;font-size:22px;line-height:1.3;text-align:center}
.finder .near{display:flex;align-items:center;justify-content:center;gap:10px}
.finder .near::before,.finder .near::after{content:"";width:42px;height:1px;background:var(--white)}
.finder label{display:block;font-size:12px;margin-top:10px}
.finder .field{height:32px;background:#fff;margin-top:4px;font-size:11px;color:#999;padding:6px 10px;display:flex;justify-content:space-between}
.finder .btn{margin-top:24px;height:40px;background:var(--red);color:#fff;text-align:center;font-family:"Montserrat",sans-serif;font-weight:500;font-size:15px;line-height:40px;text-transform:uppercase}

.article{left:778px;width:294px;height:118px;border:1px solid #dedede;background:#fff}
.article .thumb{position:absolute;left:0;top:0;width:146px;height:116px}
.article .txt{position:absolute;left:160px;top:14px;right:8px;font-size:13px;line-height:1.35;color:var(--ink)}
.article .more{display:block;color:var(--teal-text);font-size:11px;margin-top:6px}

.cats{left:768px;top:2185px;width:304px;height:882px;border:1px solid #dedede}
.cats h4{height:50px;background:var(--purple);color:#fff;font-family:"Montserrat",sans-serif;font-weight:500;font-size:18px;line-height:50px;padding-left:26px}
.cats ul{list-style:none;padding:14px 0 0 26px}
.cats li{font-size:12px;color:#555;height:30.8px;display:flex;align-items:center;gap:10px}
.cats li::before{content:"";width:0;height:0;border-left:6px solid var(--teal-dark);border-top:4px solid transparent;border-bottom:4px solid transparent}

/* footer */
.footer{left:0;top:3154px;width:1200px;height:297px;background:var(--grey-bg);border-top:1px solid #e4e4e4}
.footer .brand{left:134px;top:76px;gap:10px}
.footer .brand .mark{width:44px;height:44px}
.footer .brand .name{font-size:22px}
.footer .brand .tagline{font-size:10px}
.fcol{position:absolute;top:56px;font-size:12.5px;line-height:1.95;color:#666}
.fcol h5{font-family:"Montserrat",sans-serif;font-weight:600;font-size:15px;color:var(--teal-text);margin-bottom:6px}
.social{display:flex;gap:8px;margin-top:8px}
.social span{width:30px;height:30px;border-radius:50%;background:var(--teal-dark)}
.copyright{left:0;top:3451px;width:1200px;height:62px;background:#e9e9e9;text-align:center;line-height:62px;font-size:12px;color:#777}
</style>
</head>
<body>

<div class="abs top-bar">
  <a class="associate" href="#">Join Our Associate Program →</a>
  <nav class="top-links"><a href="#">Home</a><a href="#">Cart</a><a href="#">Blog</a><a href="#">Resources</a><a href="#">Contact</a></nav>
</div>

<header>
  <div class="abs brand">
    <span class="mark"></span>
    <div><div class="name">The Kelvale Clinic</div><div class="tagline">supporting couples to grow closer together</div></div>
  </div>
  <div class="abs search">
    <svg width="14" height="14" viewBox="0 0 14 14"><circle cx="6" cy="6" r="4.5" fill="none" stroke="#999" stroke-width="1.5"/><line x1="9.3" y1="9.3" x2="13" y2="13" stroke="#999" stroke-width="1.5"/></svg>
    Search Here
  </div>
  <div class="abs call">
    <div class="label">Call Us Now</div>
    <div class="num"><svg width="18" height="18" viewBox="0 0 24 24"><path fill="#2f9c9c" d="M6.6 10.8a15.2 15.2 0 0 0 6.6 6.6l2.2-2.2a1 1 0 0 1 1-.25 11.4 11.4 0 0 0 3.6.57 1 1 0 0 1 1 1V20a1 1 0 0 1-1 1A17 17 0 0 1 3 4a1 1 0 0 1 1-1h3.5a1 1 0 0 1 1 1c0 1.25.2 2.45.57 3.57a1 1 0 0 1-.25 1z"/></svg>1300 555 014</div>
  </div>
</header>

<nav class="abs main-nav">
  <a href="#">Counselling<br>Types</a>
  <a href="#">Relationship Counselling<br>Locations</a>
  <a href="#">Sex Therapy<br>Locations</a>
  <a href="#">About Us</a>
  <a href="#">Quizzes</a>
  <a href="#">FAQ's</a>
  <a href="#">Contact</a>
</nav>

<section class="abs hero" role="img" aria-label="Photo of a smiling couple close together">
  <h1>Sex Therapy Sydney</h1>
</section>

<!-- main content -->
<h2 class="abs main page-title" style="top:600px">8 Locations</h2>
<div class="abs portrait" role="img" aria-label="Circular photo of a couple embracing"></div>
<div class="abs main" style="top:656px;width:315px">
  <p>There is not a relationship alive that hasn't occasionally had a struggle with some aspect of their sexual union. Sex and lovemaking can be both the most delectable or disastrous part of our life and our relationship.</p>
  <p>It's because Sex satisfies us in so many ways; We can express our love; we can have great fun; we can enjoy the erotic adventure; we can feel connected; we can revel in ravishing each other and surrendering to the ecstasy of it all.</p>
</div>
<div class="abs main" style="top:910px">
  <p>When our sex and lovemaking is great, it can provide the glue that keeps us feeling deeply and physically connected with each other, enabling us to better weather many other kinds of relationship storms.</p>
</div>
<div class="abs main" style="top:1012px">
  <p class="lead" style="margin-bottom:4px">Sex in a relationship is a huge paradox.</p>
  <p>When it is good and fulfilling, it does play a small but positive role in our relationship (about 15 – 20%); BUT when our sex and lovemaking is NOT satisfying, it becomes an enormous drain and negative role. (from 50 to 75%)</p>
</div>

<h3 class="abs main alert" style="top:1170px">You are not the only ones with sexual issues.</h3>
<div class="abs main" style="top:1220px">
  <p>Research has shown that close to 45% of couples have issues with sexual desire, arousal, orgasm or satisfaction.</p>
  <p>Even though it is easy to assume to the contrary, sexual issues are rarely a simple performance problem with a simple cure. They are usually caused from a combination physical, psychological, and relationship components and can result in much emotional suffering and distress.</p>
  <p>Although sex is a common topic for sexual jokes, in reality most couples don't really talk much about what they do and don't like with each other, and very few people are actually educated on how to have a healthy lively sex life.</p>
</div>

<h3 class="abs main alert" style="top:1500px;width:560px">Does being in a long term relationship naturally diminish your sexual satisfaction?</h3>
<div class="abs main" style="top:1585px">
  <p>It is often assumed that if you have been together for a long time, that you can't expect to continue to have a satisfying, exciting sex life, but nothing could be further from the truth.</p>
  <p>In reality, the opposite can be true – couples who have been in a committed relationship for 15 years or longer can actually have the best sex of all!</p>
</div>

<h3 class="abs main alert" style="top:1750px">Our Sydney Team of Psychologists</h3>
<div class="abs main" style="top:1798px">
  <p>7 of our Sydney Relationship Psychologists, (Carina, Selma, Marisa, Delphine, Lorna, Mirella, and Annika) also specialise in Sex Therapy in addition to couple and marriage counselling.</p>
  <p>Our experience show us that on many occasions our sex life and our relationships are intricately linked, so having skills and training in both fields as therapists allows us to get the the core of any combined problem and help you create both a better sex life and better relationship.</p>
  <p>As Psychologists, you are also able to receive Medicare rebates for these sessions with us, through Mental Health Care Plans from your GP.</p>
  <p>We have written blog articles on many of the common sexual problems like low libido, differing libidos, difficulty orgasming, premature ejaculation, erectile dysfunction, porn addiction, the truth about medication, and maintaining desire.</p>
</div>

<h3 class="abs main section" style="top:2134px">Our Sydney Sex Therapy Offices:</h3>
<div class="abs main" style="top:2190px">
  <p>To make any enquiries or bookings with us, please phone 1300 555 014 and our friendly receptionists will help you. Sex Therapy (and Couple relationship) sessions are 50 mins</p>
  <p>Cost: $160 ($175 for after hours sessions or for all sessions at CBD locations)</p>
  <p style="margin-bottom:4px">Private Health Insurance Rebates apply, and Medicare Rebates may apply.</p>
  <p>(please check for details)</p>
</div>

<h3 class="abs main section" style="top:2370px;left:134px">Relationship Counselling Sydney</h3>
<div class="abs offices">
  <div class="office"><strong>Sydney CBD (George St)</strong>Suite 412, Level 4,<br>218 Harbour St<br>Sydney &nbsp; 2000</div>
  <div class="office"><strong>Riverstone</strong>Riverbend Health &amp; Wellness Centre<br>31 Bellhaven Parade<br>Riverstone &nbsp; 2765</div>
  <div class="office"><strong>Green Square (Rosebery)</strong>Suite B2, Level 1, Linden House<br>44 Ashcroft Ave<br>Rosebery &nbsp; 2018</div>
  <div class="office"><strong>Parramatta</strong>Level 3<br>18 Marlow Street<br>Parramatta &nbsp; 2151</div>
  <div class="office"><strong>Penrith</strong>96 Tallis Street<br>Penrith &nbsp; 2750</div>
  <div class="office"><strong>Crows Nest</strong>Suite 105<br>62 Wexford St<br>Crows Nest &nbsp; 2065</div>
  <div class="office"><strong>Mona Vale</strong>27 Coral Bay Rd<br>Mona Vale &nbsp; 2103</div>
  <div class="office"><strong>Windsor Downs (Lorna)</strong>9 Pemberton Lane<br>Windsor Downs 2756</div>
</div>

<!-- sidebar -->
<aside>
  <div class="abs finder">
    <h4>Find Our Psychologist<span class="near">Near You</span></h4>
    <label>Type of Counselling</label>
    <div class="field">Select <span>⌄</span></div>
    <label>Location</label>
    <div class="field"></div>
    <label>Postcode</label>
    <div class="field"></div>
    <div class="btn">Search</div>
  </div>

  <div class="abs article" style="top:991px"><div class="thumb" role="img" aria-label="Photo of a worried woman" style="background:linear-gradient(120deg,#8a7466,#d9cfc6)"></div><div class="txt">What can I do if I'm living with a Narcissist?<span class="more">Read More</span></div></div>
  <div class="abs article" style="top:1118px"><div class="thumb" role="img" aria-label="Photo of a distressed person" style="background:linear-gradient(120deg,#4a3a36,#a58c80)"></div><div class="txt">Are You Living With a Steamroller?<span class="more">Read More</span></div></div>
  <div class="abs article" style="top:1246px"><div class="thumb" role="img" aria-label="Photo of a couple arguing" style="background:linear-gradient(120deg,#c9bfb7,#6e5d55)"></div><div class="txt">Did Your Relationship Start on Rocky Ground?<span class="more">Read More</span></div></div>
  <div class="abs article" style="top:1385px"><div class="thumb" role="img" aria-label="Photo of a couple on a sofa" style="background:linear-gradient(120deg,#e2d8cc,#a98a72)"></div><div class="txt">Why am I with a Narcissist?<span class="more">Read More</span></div></div>
  <div class="abs article" style="top:1512px"><div class="thumb" role="img" aria-label="Photo of a couple talking" style="background:linear-gradient(120deg,#b7c4c9,#5f6e72)"></div><div class="txt">Letter for a Partner Doubtful About Relationship Counselling<span class="more">Read More</span></div></div>
  <div class="abs article" style="top:1643px"><div class="thumb" role="img" aria-label="Photo of two hands reaching out" style="background:linear-gradient(120deg,#d6c4b2,#8c6e58)"></div><div class="txt">What Are You Like In a Relationship?<span class="more">Read More</span></div></div>
  <div class="abs article" style="top:1771px"><div class="thumb" role="img" aria-label="Photo of a thoughtful woman" style="background:linear-gradient(120deg,#3d3633,#9d8a7f)"></div><div class="txt">How Do I Know If I'm With a Narcissist?<span class="more">Read More</span></div></div>
  <div class="abs article" style="top:1900px"><div class="thumb" role="img" aria-label="Photo of a couple sitting apart" style="background:linear-gradient(120deg,#c4b2a2,#74604f)"></div><div class="txt">Do You Wonder Why You and Your Partner Are Together?<span class="more">Read More</span></div></div>
  <div class="abs article" style="top:2026px"><div class="thumb" role="img" aria-label="Photo of a busy professional" style="background:linear-gradient(120deg,#8e7a6c,#d8cabc)"></div><div class="txt">Is Your Pursuit of Success Sabotaging Your Relationships That Matter Most?<span class="more">Read More</span></div></div>

  <div class="abs cats">
    <h4>Blogs Categories</h4>
    <ul>
      <li>Affairs</li><li>Assertiveness</li><li>Attachment</li><li>Break up</li><li>Communication</li>
      <li>Compatibility</li><li>Controlling</li><li>Couples counselling</li><li>Empathy</li><li>Enneagram</li>
      <li>Financial stress</li><li>Individual counselling for relationships</li><li>Infertility</li><li>Intimacy</li><li>Marriage-counselling</li>
      <li>Narcissism</li><li>Personal growth</li><li>Personality</li><li>psychological-wellbeing</li><li>Psychologist Interviews</li>
      <li>Relationship counselling</li><li>Relationship happiness</li><li>Relationship problems</li><li>Singles</li><li>Uncategorized</li>
    </ul>
  </div>
</aside>

<footer class="abs footer">
  <div class="abs brand">
    <span class="mark"></span>
    <div><div class="name">The Kelvale Clinic</div><div class="tagline">supporting couples to grow closer together</div></div>
  </div>
  <div class="fcol" style="left:452px"><h5>QUICK LINKS</h5>Home<br>About Us<br>Our Blogs<br>Shop Cart<br>Contact Us</div>
  <div class="fcol" style="left:620px"><h5>RESOURCES</h5>Counselling Type<br>Sex Therapy<br>Quizzes<br>FAQ<br>Relationship Counselling</div>
  <div class="fcol" style="left:824px"><h5>CONTACT US</h5>140 Kelvale Drive Suite 7<br>1300 555 014<br>Email: info@kelvaleclinic.com.au
    <div class="social"><span></span><span></span><span></span><span></span></div>
  </div>
</footer>
<div class="abs copyright">© 2017 Company Name &nbsp;All right reserved</div>

</body>
</html>
```